Business Card for a mobile physiotherapy company

I need a layout for a business card for a mobile physiotherapy company.
Slogan is "Mobile Physiotherapy - Your Road To Recovery"
Phone number is 867-555-0142
Email VardenTherapy@postnest.ca (subject to change with website)
Website www.VardenTherapy.ca
My name and credentials: Luke Varden Luke Varden, BSc(kin), MPT, CAFCI, IMS
Information maybe included: Direct Billing, Services including Physiotherapy, IMS, acupuncture
Maybe include facebook and instagram logos
One side with the logo clean and sharp
Other side with details, try not to look too busy, keep everything concise

```html
<!DOCTYPE html>
<html lang="en">
<head>
<meta charset="utf-8">
<title>Varden Therapy – Business Card</title>
<link rel="stylesheet" href="https://fonts.googleapis.com/css2?family=Montserrat:wght@400;500;600;700;800&display=swap">
<style>
  :root {
    --green: #0f5c4f;
    --green-light: #2f7a6c;
    --navy: #26407a;
    --white: #ffffff;
    --paper: #f6f7f7;
    --ink: #222222;
    --stage: #3a3a3c;
    --card-w: 560px;
    --card-h: 320px;
  }
  * { box-sizing: border-box; margin: 0; padding: 0; }
  html, body { width: 1200px; height: 997px; overflow: hidden; }
  body {
    background: var(--stage);
    font-family: "Montserrat", Arial, sans-serif;
    display: flex;
    flex-direction: column;
    align-items: center;
    justify-content: center;
    gap: 70px;
  }
  .card {
    position: relative;
    width: var(--card-w);
    height: var(--card-h);
    border-radius: 22px;
    overflow: hidden;
    box-shadow: 0 14px 30px rgba(0,0,0,.45);
  }

  /* Back side */
  .card-back { background: var(--green); color: var(--white); }
  .back-brand {
    position: absolute; left: 0; right: 0; top: 78px;
    text-align: center;
  }
  .brand-name {
    font-weight: 800;
    font-size: 48px;
    letter-spacing: 4px;
    line-height: 1;
    text-transform: uppercase;
  }
  .brand-sub {
    font-weight: 800;
    font-size: 22px;
    letter-spacing: 12px;
    text-transform: uppercase;
    margin-top: 8px;
  }
  .back-services {
    position: absolute; left: 0; right: 0; top: 196px;
    text-align: center;
  }
  .services-label {
    display: flex; align-items: center; gap: 12px;
    padding: 0 28px;
    font-size: 12px; font-weight: 700; letter-spacing: 1px;
  }
  .services-label::before, .services-label::after {
    content: ""; flex: 1; height: 1px; background: rgba(255,255,255,.75);
  }
  .services-list {
    margin-top: 10px;
    font-size: 12px; font-weight: 500; letter-spacing: .8px;
  }
  .back-rule {
    position: absolute; left: 28px; right: 28px; bottom: 34px;
    height: 1px; background: rgba(255,255,255,.55);
  }

  /* Front side */
  .card-front { background: var(--paper); color: var(--ink); }
  .front-brand {
    position: absolute; left: 0; right: 0; top: 46px;
    text-align: center; color: var(--green);
  }
  .front-brand .brand-name { font-size: 40px; }
  .front-brand .brand-sub { font-size: 18px; letter-spacing: 10px; }
  .front-rule {
    position: absolute; right: 26px; top: 62px; width: 120px;
    height: 1px; background: var(--ink);
  }
  .person {
    position: absolute; left: 30px; top: 150px; right: 150px;
  }
  .person-name {
    display: flex; align-items: center; gap: 4px;
    color: var(--green); font-weight: 700; font-size: 16px;
    text-transform: uppercase; letter-spacing: .5px;
  }
  .person-name::after { content: ""; flex: 1; height: 1px; background: var(--ink); }
  .person-credentials { font-size: 11.5px; font-weight: 500; margin-top: 2px; }
  .contact-list {
    position: absolute; left: 30px; top: 200px;
    list-style: none;
  }
  .contact-list li {
    display: flex; align-items: center; gap: 10px;
    font-size: 13px; font-weight: 500; height: 20px;
  }
  .contact-list .web { font-weight: 700; color: var(--green); }
  .contact-icon {
    width: 15px; height: 15px; border-radius: 50%;
    background: var(--navy);
    display: flex; align-items: center; justify-content: center;
  }
  .social {
    position: absolute; right: 26px; top: 208px;
    display: flex; align-items: center; gap: 6px;
    color: var(--navy); font-weight: 700; font-size: 14px;
  }
  .social-dot { width: 12px; height: 12px; border-radius: 50%; background: var(--green); }
  .front-bands { position: absolute; inset: 0; }
  .slogan {
    position: absolute; right: 18px; bottom: 28px; width: 210px;
    text-align: center; color: var(--white);
    font-size: 8.5px; font-weight: 700; letter-spacing: .3px;
    text-transform: uppercase;
  }
</style>
</head>
<body>

  <section class="card card-back" aria-label="Business card, back">
    <div class="back-brand">
      <div class="brand-name">Varden</div>
      <div class="brand-sub">Therapy</div>
    </div>
    <div class="back-services">
      <div class="services-label">SERVICES INCLUDING</div>
      <div class="services-list">DIRECT BILLING, PHYSIOTHERAPY, IMS, ACUPUNCTURE</div>
    </div>
    <div class="back-rule"></div>
  </section>

  <section class="card card-front" aria-label="Business card, front">
    <svg class="front-bands" viewBox="0 0 560 320" width="560" height="320" aria-hidden="true">
      <path d="M0 288 H296 C312 288 316 260 334 260 H346 C326 260 322 300 302 300 H0 Z" fill="var(--navy)"/>
      <path d="M0 302 H304 C326 302 330 262 352 262 H560 V320 H0 Z" fill="var(--green)"/>
    </svg>

    <div class="front-brand">
      <div class="brand-name">Varden</div>
      <div class="brand-sub">Therapy</div>
    </div>
    <div class="front-rule"></div>

    <div class="person">
      <div class="person-name">Luke Varden</div>
      <div class="person-credentials">BSc(kin), MPT, CAFCI, IMS</div>
    </div>

    <ul class="contact-list">
      <li>
        <span class="contact-icon">
          <svg width="9" height="9" viewBox="0 0 10 10" aria-hidden="true"><path d="M2 1 L4 3 L3 4 C3.6 5.4 4.6 6.4 6 7 L7 6 L9 8 L8 9 C4.5 9 1 5.5 1 2 Z" fill="#fff"/></svg>
        </span>867-555-0142
      </li>
      <li>
        <span class="contact-icon">
          <svg width="9" height="9" viewBox="0 0 10 10" aria-hidden="true"><rect x="1" y="2" width="8" height="6" fill="none" stroke="#fff" stroke-width="1"/><path d="M1 2 L5 5.5 L9 2" fill="none" stroke="#fff" stroke-width="1"/></svg>
        </span>VardenTherapy@postnest.ca
      </li>
      <li class="web">
        <span class="contact-icon">
          <svg width="9" height="9" viewBox="0 0 10 10" aria-hidden="true"><circle cx="5" cy="5" r="3.8" fill="none" stroke="#fff" stroke-width="1"/><path d="M1.2 5 H8.8 M5 1.2 V8.8" stroke="#fff" stroke-width=".8"/></svg>
        </span>www.VardenTherapy.ca
      </li>
    </ul>

    <div class="social"><span class="social-dot"></span>/VardenTherapy</div>

    <div class="slogan">Mobile Physiotherapy - Your Road To Recovery</div>
  </section>

</body>
</html>
```